Candy Bar Desgin

We need a postcard desgin for my new company. I just started a Candy bar/buffet called Sweet table By Mimi. My motto is Sweet Table by Mimi for the tiny tab. I will be attending a bridal show where I can display my work so there will be brides there. So I want something to pop. Maybe can add vases filled with candy. Add 20% off an event you book for attending the bridal show. I want colors. Candy colors. My company also do chocolate fountain bars as well. My website to add is www.sweettablebymimi.com
Email sweettablebymimi@fizzmail.com
Phone 323-555-0184

Target Market(s)

Brides

Industry/Entity Type

It Company

Requirements
Must have
• Must have my motto. And my contact information
Should not have
• No old style don't like times new roman. Use fun fonts

```html
<!DOCTYPE html>
<html lang="en">
<head>
<meta charset="utf-8">
<title>Sweet Table by Mimi – Postcard</title>
<link href="https://fonts.googleapis.com/css2?family=Dancing+Script:wght@700&family=Lato:ital,wght@0,400;0,700;0,900;1,400;1,700;1,900&family=Open+Sans:wght@400;600&display=swap" rel="stylesheet">
<style>
  :root{
    --backdrop:#2b2b2b;
    --card:#ffffff;
    --pink:#ec8f86;
    --pink-deep:#e0665f;
    --pink-soft:#f6c9c2;
    --stamp:#fbe1dc;
    --red:#e0203a;
    --red-dark:#b8142b;
    --yellow:#f7d21a;
    --ink:#1d1d1d;
    --brown:#6b2418;
    --white:#ffffff;
  }
  *{margin:0;padding:0;box-sizing:border-box}
  html,body{width:1200px;height:1098px;overflow:hidden}
  body{background:var(--backdrop);position:relative;font-family:'Lato',sans-serif}

  .card{position:absolute;background:var(--card);overflow:hidden;box-shadow:0 6px 18px rgba(0,0,0,.45)}

  /* ---------- back side ---------- */
  .card-back{left:65px;top:47px;width:690px;height:535px}
  .back-header{position:absolute;left:0;top:0;width:166px;height:111px;
    background:linear-gradient(100deg,var(--pink-deep) 0%,var(--pink) 100%)}
  .back-swoosh{position:absolute;left:0;top:0;width:690px;height:260px}
  .welcome{position:absolute;left:34px;top:28px;font-family:'Dancing Script',cursive;
    font-size:23px;line-height:30px;color:var(--red-dark);text-shadow:0 0 2px #fff,0 0 3px #fff;white-space:nowrap}
  .stamp-box{position:absolute;left:530px;top:28px;width:130px;height:128px;background:var(--stamp)}
  .cell{position:absolute;width:166px;height:110px}
  .photo{background:linear-gradient(135deg,#f3d7cf,#e9a9a0 50%,#c9786c)}
  .photo.buffet{background:linear-gradient(135deg,#7b9c7a,#e7a0b3 55%,#f2d5dc)}
  .photo.fountain{background:linear-gradient(135deg,#e7d9c6,#8a5a3a 45%,#d8423a 80%,#f1b84a)}
  .event-list{list-style:none;background:var(--pink);color:var(--white);font-family:'Open Sans',sans-serif;
    font-size:13.5px;line-height:19px;padding:15px 0 0 14px;white-space:nowrap}
  .event-list.left{padding:8px 0 0 23px;font-size:13px;
    background:linear-gradient(110deg,var(--pink-deep),var(--pink) 70%)}
  .call-cell{background:var(--pink);text-align:center;padding-top:4px}
  .call-title{font-weight:900;font-style:italic;font-size:21px;color:var(--brown)}
  .call-phone{font-weight:900;font-style:italic;font-size:20px;color:var(--white);line-height:22px}
  .call-web{font-style:italic;font-size:12px;color:var(--white)}
  .call-jars{position:absolute;left:35px;bottom:4px;width:96px;height:38px;border-radius:4px;
    background:linear-gradient(90deg,#e7523c,#f2c940 30%,#b8344e 60%,#a52234)}
  .corner-block{position:absolute;left:0;top:441px;width:86px;height:94px;background:var(--pink)}
  .motto{position:absolute;left:380px;top:300px;width:290px;text-align:center;
    font-family:'Dancing Script',cursive;font-size:24px;line-height:30px;color:var(--red-dark)}
  .offer{position:absolute;left:400px;top:385px;width:250px;padding:12px 10px;text-align:center;
    background:var(--pink);color:var(--white);border-radius:6px}
  .offer-big{font-weight:900;font-style:italic;font-size:30px;line-height:34px;color:var(--white)}
  .offer-note{font-size:13px;line-height:17px}

  /* ---------- front side ---------- */
  .card-front{left:431px;top:533px;width:714px;height:553px}
  .front-swoosh{position:absolute;left:0;top:0;width:714px;height:250px}
  .front-title{position:absolute;left:0;top:36px;width:100%;text-align:center;
    font-weight:900;font-size:56px;line-height:64px;color:var(--red)}
  .front-intro{position:absolute;left:45px;top:123px;width:624px;text-align:center;
    font-style:italic;font-size:15.5px;line-height:21.5px;color:var(--ink)}
  .front-reach{position:absolute;left:0;top:197px;width:100%;text-align:center;
    font-style:italic;font-size:19px;color:var(--red)}
  .front-photo{position:absolute;left:0;top:240px;width:714px;height:246px;
    background:linear-gradient(160deg,#f0ede9 0%,#f4b54a 30%,#e55d6b 55%,#f7dbe3 75%,#9ec7ea 100%)}
  .front-footer{position:absolute;left:0;top:470px;width:714px;height:83px}
  .footer-phone{position:absolute;left:33px;top:490px;font-weight:900;font-style:italic;
    font-size:27px;color:var(--white)}
  .footer-email{position:absolute;left:33px;top:527px;font-style:italic;font-size:14.5px;color:var(--white)}
  .footer-address{position:absolute;right:32px;top:497px;font-size:15px;color:var(--white)}
  .footer-web{position:absolute;right:32px;top:520px;font-style:italic;font-size:17px;color:var(--white)}
</style>
</head>
<body>

<section class="card card-back">
  <div class="back-header"></div>
  <svg class="back-swoosh" viewBox="0 0 690 260" role="img" aria-label="Soft rainbow swoosh decoration">
    <defs>
      <linearGradient id="backBand" x1="0" y1="0" x2="0" y2="1">
        <stop offset="0" stop-color="#f47a8a"/>
        <stop offset=".3" stop-color="#f5d75a"/>
        <stop offset=".55" stop-color="#8fd08a"/>
        <stop offset=".8" stop-color="#7cc3ec"/>
        <stop offset="1" stop-color="#f39ac6"/>
      </linearGradient>
    </defs>
    <path d="M166 0 L331 0 C400 40 460 150 690 80 L690 140 C460 210 380 150 331 111 L166 111 Z" fill="url(#backBand)" opacity=".35"/>
  </svg>
  <p class="welcome">Welcome to Sweet Table by Mimi.<br>Serving any where your party takes me!</p>
  <div class="stamp-box"></div>

  <div class="cell photo" style="left:0;top:111px" role="img" aria-label="Photo of pink-dipped crispy rice treats on a platter"></div>
  <ul class="cell event-list" style="left:166px;top:111px">
    <li>*Birthday Parties</li><li>*Weddings</li><li>*Graduations</li><li>*Sweet 16s</li>
  </ul>
  <ul class="cell event-list left" style="left:0;top:221px">
    <li>*Baby showers</li><li>*Bridal Showers</li><li>*Holiday Parties</li><li>*Corporate Events</li><li>*Bar and Bat Mitzvahs</li>
  </ul>
  <div class="cell photo buffet" style="left:166px;top:221px" role="img" aria-label="Photo of a pink candy buffet with glass jars"></div>
  <div class="cell photo fountain" style="left:0;top:331px" role="img" aria-label="Photo of a chocolate fountain with fruit skewers"></div>
  <div class="cell call-cell" style="left:166px;top:331px">
    <div class="call-title">Call Us Now</div>
    <div class="call-phone">323-555-0184</div>
    <div class="call-web">www.sweettablebymimi.com</div>
    <div class="call-jars" role="img" aria-label="Small picture of candy jars"></div>
  </div>
  <div class="corner-block"></div>

  <p class="motto">Sweet Table by Mimi<br>for the tiny tab</p>
  <div class="offer">
    <div class="offer-big">20% OFF</div>
    <div class="offer-note">any event you book for attending the bridal show</div>
  </div>
</section>

<section class="card card-front">
  <svg class="front-swoosh" viewBox="0 0 714 250" preserveAspectRatio="none" role="img" aria-label="Soft rainbow swoosh decoration">
    <defs>
      <linearGradient id="frontBand" x1="0" y1="0" x2="0" y2="1">
        <stop offset="0" stop-color="#f47a8a"/>
        <stop offset=".3" stop-color="#f5d75a"/>
        <stop offset=".55" stop-color="#8fd08a"/>
        <stop offset=".8" stop-color="#7cc3ec"/>
        <stop offset="1" stop-color="#f39ac6"/>
      </linearGradient>
    </defs>
    <path d="M0 110 C140 20 430 100 714 10 L714 90 C430 170 160 80 0 220 Z" fill="url(#frontBand)" opacity=".22"/>
  </svg>
  <h1 class="front-title">Sweet Table by Mimi</h1>
  <p class="front-intro">Sweet Table by Mimi will add fun and color to your next event and bring you and your guest back to your childhood roots. I promise it will be visual feast filled with color, aroma and the magic that only candy brings.</p>
  <p class="front-reach">I provide my candy bars to any city your event is needed at.</p>
  <div class="front-photo" role="img" aria-label="Photo of a colorful candy table with jars, popcorn, cookies and cake pops"></div>
  <svg class="front-footer" viewBox="0 0 714 83" preserveAspectRatio="none" aria-hidden="true">
    <path d="M0 8 C150 -4 260 18 357 14 C470 10 560 -6 714 6 L714 83 L0 83 Z" fill="var(--yellow)"/>
    <path d="M0 14 C150 2 260 24 357 20 C470 16 560 0 714 12 L714 83 L0 83 Z" fill="var(--red)"/>
  </svg>
  <div class="footer-phone">323-555-0184</div>
  <div class="footer-email">Email sweettablebymimi@fizzmail.com</div>
  <div class="footer-address">Pasadena California United States 91101</div>
  <div class="footer-web">www.sweettablebymimi.com</div>
</section>

</body>
</html>
```